Brand Identity Stationary Package

Hello I'm looking for a full branding package for my Property Management Company. I have a logo but looking to have the following
Business Card
Email signature
Facebook cover photo
Letterhead (word.doc)
#10 Envelope
Pocket Folder - link to 9x12 pocket folder design specs https://www.printorbit-example.ca/marketing-materials/presentation-folders
would like everything to match and be brand identifiable. The company looks after residential properties/apartments and some commercial properties. Attached is a zip of the files.
For Business Card
Name: Gareth Lindqvist
Position: Operations Manager
Number: 1 (555) 384-2917
Email: Gareth@harborkey-example.ca
Website: Harborkey-example.ca
Property Management

```html
<!DOCTYPE html>
<html lang="en">
<head>
<meta charset="utf-8">
<title>Harborkey Property Management — #10 Envelope</title>
<link rel="stylesheet" href="https://fonts.googleapis.com/css2?family=Source+Sans+3:wght@400;600&display=swap">
<style>
  :root {
    --backdrop: #d0cfcf;
    --paper: #f2f1f1;
    --paper-light: #ffffff;
    --brand-green: #80a642;
    --ink: #111111;
    --shadow: rgba(0, 0, 0, 0.28);
  }
  * { margin: 0; padding: 0; box-sizing: border-box; }
  html, body {
    width: 1200px;
    height: 1050px;
    overflow: hidden;
    background: var(--backdrop);
    font-family: "Source Sans 3", "Myriad Pro", Arial, sans-serif;
  }
  .canvas {
    position: relative;
    width: 1200px;
    height: 1050px;
  }
  .envelope {
    position: absolute;
    left: 145px;
    width: 910px;
    height: 390px;
    background: radial-gradient(ellipse at 50% 60%, var(--paper-light) 0%, var(--paper) 70%);
    box-shadow: 0 14px 18px -6px var(--shadow);
    overflow: hidden;
  }
  .envelope--back { top: 105px; }
  .envelope--front { top: 555px; }
  .envelope__art {
    position: absolute;
    inset: 0;
    width: 910px;
    height: 390px;
  }
  .brand-name {
    position: absolute;
    font-weight: 600;
    letter-spacing: 0.12em;
    line-height: 1;
    white-space: nowrap;
  }
  .envelope--back .brand-name {
    left: 0;
    right: 0;
    top: 40px;
    text-align: center;
    font-size: 46px;
    color: var(--paper-light);
  }
  .envelope--front .brand-name {
    left: 52px;
    top: 60px;
    font-size: 40px;
    color: var(--ink);
  }
  .contact-list {
    position: absolute;
    left: 52px;
    top: 148px;
    list-style: none;
  }
  .contact-list__item {
    display: flex;
    align-items: center;
    height: 26px;
    font-size: 21px;
    color: var(--ink);
  }
  .contact-list__icon {
    width: 16px;
    height: 16px;
    margin-right: 12px;
    fill: var(--brand-green);
  }
</style>
</head>
<body>
<main class="canvas">

  <section class="envelope envelope--back" aria-label="Envelope back with flap">
    <svg class="envelope__art" viewBox="0 0 910 390" aria-hidden="true">
      <path d="M0,0 H910 L885,91 Q870,131 833,131 H77 Q40,131 25,91 Z" fill="var(--brand-green)"/>
    </svg>
    <div class="brand-name">HARBORKEY</div>
  </section>

  <section class="envelope envelope--front" aria-label="Envelope front">
    <svg class="envelope__art" viewBox="0 0 910 390" aria-hidden="true">
      <path d="M0,246 Q455,430 910,243 V390 H0 Z" fill="var(--brand-green)"/>
      <path d="M47,255 Q446,408 845,261 Q446,386 47,255 Z" fill="var(--ink)"/>
    </svg>

    <div class="brand-name">HARBORKEY</div>

    <ul class="contact-list">
      <li class="contact-list__item">
        <svg class="contact-list__icon" viewBox="0 0 16 16" aria-hidden="true">
          <path d="M1,6 Q1,3 8,3 Q15,3 15,6 V7 H11 V5.5 H5 V7 H1 Z"/>
          <path d="M4,7 H12 L14,13 H2 Z"/>
        </svg>
        1 (555) 384-2917
      </li>
      <li class="contact-list__item">
        <svg class="contact-list__icon" viewBox="0 0 16 16" aria-hidden="true">
          <path d="M1,3 H15 L8,9 Z"/>
          <path d="M1,4.5 L8,10.5 L15,4.5 V13 H1 Z"/>
        </svg>
        Gareth@harborkey-example.ca
      </li>
      <li class="contact-list__item">
        <svg class="contact-list__icon" viewBox="0 0 16 16" aria-hidden="true">
          <circle cx="8" cy="8" r="7"/>
          <path d="M4,4 Q7,5 6,8 Q4,9 5,12 Q3,10 3,7 Z M9,3 Q12,4 12,7 Q10,8 11,11 Q9,9 9,6 Z" fill="var(--paper-light)"/>
        </svg>
        www.Harborkey-example.ca
      </li>
    </ul>
  </section>

</main>
</body>
</html>
```